Coastline Premier Retreats Business Card Design

Design a business card for Coastline Premier Retreats. Look at the website for colors and reference. Card should have logo, name, title, office number, mobile number, email, URL and a tagline like, "Luxury Hotel & Resort Email Marketing" (This might change).

https://www.coastlinepremierretreats.example

The rest I will leave up to your imagination.

Contact Information for Business Card

Logo, name, title, office number, mobile number, email, URL and a tagline like, "Luxury Hotel & Resort Email Marketing" (This might change).

```html
<!DOCTYPE html>
<html lang="en">
<head>
<meta charset="utf-8">
<title>Coastline Premier Retreats – Business Card</title>
<link href="https://fonts.googleapis.com/css2?family=Montserrat:wght@400;600;700&display=swap" rel="stylesheet">
<style>
  :root {
    --bg: #7b7b7b;
    --orange: #e46c00;
    --gold: #f0c84a;
    --paper: #f5f5f5;
    --ink: #141414;
    --muted: #555555;
    --rule: #b5b5b5;
  }
  * { margin: 0; padding: 0; box-sizing: border-box; }
  html, body { width: 1200px; height: 900px; overflow: hidden; }
  body {
    background: var(--bg);
    font-family: "Montserrat", Arial, sans-serif;
    position: relative;
  }
  .card {
    position: absolute;
    left: 320px;
    width: 560px;
    height: 320px;
    border-radius: 18px;
    box-shadow: 0 6px 18px rgba(0,0,0,0.3);
    overflow: hidden;
  }
  .card-front {
    top: 95px;
    background: var(--orange);
    display: flex;
    align-items: center;
    justify-content: center;
  }
  .brand-foil {
    color: var(--gold);
    font-weight: 700;
    font-size: 30px;
    letter-spacing: 2px;
    text-transform: uppercase;
    text-align: center;
    line-height: 1.15;
  }
  .card-back {
    top: 480px;
    background: var(--paper);
    color: var(--ink);
  }
  .brand-mark {
    position: absolute;
    top: 46px;
    left: 0;
    right: 0;
    display: flex;
    align-items: center;
    justify-content: center;
    gap: 10px;
  }
  .brand-mark .square {
    width: 14px;
    height: 14px;
    background: var(--orange);
  }
  .brand-mark .brand-name {
    font-weight: 700;
    font-size: 20px;
    letter-spacing: 1.5px;
    text-transform: uppercase;
    color: var(--ink);
  }
  .person {
    position: absolute;
    top: 128px;
    right: 336px;
    text-align: right;
    white-space: nowrap;
  }
  .person-name { font-weight: 700; font-size: 22px; }
  .person-title { font-size: 14px; color: var(--muted); margin-top: 2px; }
  .divider {
    position: absolute;
    top: 118px;
    left: 240px;
    width: 1px;
    height: 82px;
    background: var(--rule);
  }
  .contact-list {
    position: absolute;
    top: 118px;
    left: 256px;
    list-style: none;
    font-size: 11.5px;
    line-height: 20.5px;
    white-space: nowrap;
  }
  .contact-list li { display: flex; align-items: center; gap: 8px; }
  .contact-list svg { width: 12px; height: 12px; flex: none; }
  .tagline {
    position: absolute;
    bottom: 38px;
    left: 0;
    right: 0;
    text-align: center;
    font-size: 14px;
    color: var(--ink);
  }
</style>
</head>
<body>
  <section class="card card-front">
    <div class="brand-foil">Coastline<br>Premier Retreats</div>
  </section>

  <section class="card card-back">
    <div class="brand-mark">
      <span class="square"></span>
      <span class="brand-name">Coastline Premier Retreats</span>
    </div>

    <div class="person">
      <div class="person-name">Daniel Brooks</div>
      <div class="person-title">President</div>
    </div>

    <div class="divider"></div>

    <ul class="contact-list">
      <li>
        <svg viewBox="0 0 12 12" aria-hidden="true"><path d="M2.5 1 L4.5 1 L5.2 3.4 L3.9 4.4 Q5 7 7.6 8.1 L8.6 6.8 L11 7.5 L11 9.5 Q10.5 11 9 11 Q1 10 1 3 Q1 1.5 2.5 1 Z" fill="var(--orange)"/></svg>
        555.014.2000
      </li>
      <li>
        <svg viewBox="0 0 12 12" aria-hidden="true"><rect x="3" y="0.8" width="6" height="10.4" rx="1" fill="none" stroke="var(--orange)" stroke-width="1.4"/></svg>
        555.014.2001
      </li>
      <li>
        <svg viewBox="0 0 12 12" aria-hidden="true"><rect x="0.8" y="2.2" width="10.4" height="7.6" fill="var(--orange)"/><path d="M1 2.5 L6 6.5 L11 2.5" fill="none" stroke="var(--paper)" stroke-width="1"/></svg>
        info@coastlinepremierretreats.example
      </li>
      <li>
        <svg viewBox="0 0 12 12" aria-hidden="true"><circle cx="6" cy="6" r="5.2" fill="var(--orange)"/><path d="M1 6 H11 M6 1 Q3 6 6 11 M6 1 Q9 6 6 11" fill="none" stroke="var(--paper)" stroke-width="0.8"/></svg>
        www.coastlinepremierretreats.example
      </li>
    </ul>

    <p class="tagline">Luxury Hotel &amp; Resort Email Marketing</p>
  </section>
</body>
</html>
```